Business Card Design For A Cajun Seafood Restaurant

We are opening a cajun seafood restaurant in a week. We mainly serve cajun seafood which is orginally from Louisiana. We want design on both sides of a business card. I have menu on the website. You can go to www.reednkettle.example to check out our menu.

Restaurant name: Reed N' Kettle
Phone: +1 (555) 304-7712
Address: 48206 Ludlow Row, #7, Bexmoor Flats, Ca90000
Email: reednkettle@mailbox.example
Website: www.reednkettle.example

Maybe add social media icons (facebook, instagram) if looks nice on the business card.
facebook.com/reednkettle
instagram.com/reednkettle or @reednkettle

Attached is the logo and other business card samples that I like.

```html
<!DOCTYPE html>
<html lang="en">
<head>
<meta charset="utf-8">
<title>Reed N' Kettle – Business Card</title>
<link rel="stylesheet" href="https://fonts.googleapis.com/css2?family=Open+Sans:wght@400;700&display=swap">
<style>
  :root {
    --bg: #e9e6e1;
    --card-black: #0d0d0d;
    --card-black-soft: #1a1a1a;
    --orange: #ff6a00;
    --yellow: #ffd200;
    --mascot-warm: #e8631c;
    --mascot-light: #f2b51d;
    --mascot-deep: #b8420f;
    --white: #ffffff;
    --text-light: #f2f2f2;
  }
  * { box-sizing: border-box; margin: 0; padding: 0; }
  html, body { width: 1200px; height: 900px; overflow: hidden; }
  body {
    background: var(--bg);
    font-family: "Open Sans", Arial, sans-serif;
    position: relative;
  }
  .card {
    position: absolute;
    left: 300px;
    width: 600px;
    height: 343px;
    background: radial-gradient(ellipse at 60% 40%, var(--card-black-soft), var(--card-black));
    overflow: hidden;
    box-shadow: 0 6px 18px rgba(0,0,0,0.18);
  }
  .card-front { top: 72px; }
  .card-back { top: 475px; }

  .mascot-area {
    position: absolute;
    border-radius: 50% 50% 40% 40%;
    background: radial-gradient(circle at 50% 35%, var(--mascot-light) 0 22%, var(--mascot-warm) 40%, var(--mascot-deep) 80%);
  }
  .card-front .mascot-area { left: 240px; top: 52px; width: 120px; height: 120px; }
  .brand-name {
    position: absolute;
    font-weight: 700;
    color: var(--yellow);
    white-space: nowrap;
    letter-spacing: 0.5px;
    text-align: center;
  }
  .card-front .brand-name {
    left: 0; right: 0; top: 192px;
    font-size: 44px;
  }

  .card-back .mascot-area { left: 432px; top: 22px; width: 96px; height: 96px; }
  .card-back .brand-name { left: 360px; width: 240px; top: 128px; font-size: 24px; }

  .contact-list {
    position: absolute;
    left: 70px;
    top: 150px;
    list-style: none;
    color: var(--text-light);
    font-size: 15px;
    line-height: 22px;
  }
  .contact-list li { display: flex; align-items: center; gap: 10px; }
  .contact-list svg { width: 13px; height: 13px; flex: none; }

  .social {
    position: absolute;
    display: flex;
    align-items: center;
    gap: 8px;
    color: var(--text-light);
    font-size: 15px;
  }
  .social-mark {
    width: 20px; height: 20px;
    background: var(--yellow);
    border-radius: 3px;
  }
  .social-facebook { left: 380px; top: 178px; }
  .social-instagram { left: 70px; top: 220px; font-size: 17px; }
  .social-instagram .social-mark { width: 24px; height: 24px; }

  .accent-line {
    position: absolute;
    left: 0; right: 0; top: 250px;
    height: 6px;
    background: var(--yellow);
  }
  .address-band {
    position: absolute;
    left: 0; right: 0; top: 256px; bottom: 0;
    background: var(--orange);
    display: flex;
    align-items: center;
    justify-content: center;
    color: var(--white);
    font-size: 16px;
  }
</style>
</head>
<body>
  <section class="card card-front" aria-label="Business card front">
    <div class="mascot-area" role="img" aria-label="Restaurant mascot illustration"></div>
    <div class="brand-name">Reed N' Kettle</div>
  </section>

  <section class="card card-back" aria-label="Business card back">
    <div class="mascot-area" role="img" aria-label="Restaurant mascot illustration"></div>
    <div class="brand-name">Reed N' Kettle</div>

    <ul class="contact-list">
      <li>
        <svg viewBox="0 0 16 16" aria-hidden="true"><path fill="#ffd200" d="M3 1h3l1 4-2 1.5a9 9 0 0 0 4.5 4.5L11 9l4 1v3a2 2 0 0 1-2 2A12 12 0 0 1 1 3a2 2 0 0 1 2-2z"/></svg>
        +1 (555) 304-7712
      </li>
      <li>
        <svg viewBox="0 0 16 16" aria-hidden="true"><rect x="1" y="3" width="14" height="10" fill="#ffd200"/><path d="M1 3l7 6 7-6" fill="none" stroke="#0d0d0d" stroke-width="1.4"/></svg>
        reednkettle@mailbox.example
      </li>
      <li>
        <svg viewBox="0 0 16 16" aria-hidden="true"><circle cx="8" cy="8" r="7" fill="#ffd200"/><path d="M1 8h14M8 1c-3 3-3 11 0 14M8 1c3 3 3 11 0 14" fill="none" stroke="#0d0d0d" stroke-width="1"/></svg>
        www.reednkettle.example
      </li>
    </ul>

    <div class="social social-facebook"><span class="social-mark" aria-hidden="true"></span>/reednkettle</div>
    <div class="social social-instagram"><span class="social-mark" aria-hidden="true"></span>/reednkettle</div>

    <div class="accent-line"></div>
    <div class="address-band">48206 Ludlow Row, #7, Bexmoor Flats, Ca90000</div>
  </section>
</body>
</html>
```